Corvy

Electronic Repairs for OEM's Industrial electronic repairs, consumer audio visual, Projectors

Target Market(s)

manufacturer of electronics (OEM), business, Government, then Consumer

Industry/Entity Type

Electronic Repair

Contact Information for Business Card

Board Repair, Projectors

Font styles to use
Serif

Colors
0054AA
0677BA
7BADD7
CADEEF
E8F1F8

Requirements
Must have
• projector, led wall image
Nice to have
• professional looking business card.
Should not have
• unsure

```html
<!DOCTYPE html>
<html lang="en">
<head>
<meta charset="utf-8">
<title>Corvy Electronic Repairs – Business Card</title>
<link rel="stylesheet" href="https://fonts.googleapis.com/css2?family=Inter:ital,wght@0,400;0,600;0,700;1,400&display=swap">
<style>
  :root {
    --brand-deep: #0054AA;
    --brand-mid: #0677BA;
    --brand-soft: #7BADD7;
    --brand-pale: #CADEEF;
    --brand-mist: #E8F1F8;
    --ink: #2b2b2b;
    --card: #ffffff;
    --backdrop: #e9e6e2;
  }
  * { margin: 0; padding: 0; box-sizing: border-box; }
  html, body {
    width: 1200px; height: 969px; overflow: hidden;
    background: var(--backdrop);
    font-family: "Inter", Arial, sans-serif;
  }
  .card {
    position: absolute; left: 100px; top: 200px;
    width: 1000px; height: 568px;
    background: var(--card);
    border-radius: 30px;
    overflow: hidden;
    box-shadow: 0 10px 30px rgba(0,0,0,.12);
  }
  .card__panel { position: absolute; inset: 0; }
  .brand { position: absolute; left: 71px; top: 91px; }
  .brand__dot {
    position: absolute; left: 0; top: 0;
    width: 112px; height: 112px; border-radius: 50%;
    background: var(--brand-deep);
  }
  .brand__name {
    position: absolute; left: 130px; top: -8px;
    font-weight: 700; font-size: 100px; line-height: 1;
    color: var(--brand-deep); letter-spacing: 1px; white-space: nowrap;
  }
  .brand__line {
    position: absolute; left: 131px; top: 86px;
    font-weight: 700; font-size: 28px; line-height: 1;
    color: var(--brand-deep); letter-spacing: .5px; white-space: nowrap;
  }
  .intro {
    position: absolute; left: 90px; top: 262px;
    font-weight: 600; font-size: 24px; line-height: 31px;
    color: var(--brand-mid);
  }
  .services { position: absolute; left: 90px; top: 388px; list-style: none; }
  .services li {
    display: flex; align-items: center; gap: 12px;
    font-style: italic; font-size: 25px; line-height: 35px; color: var(--ink);
  }
  .services svg { width: 26px; height: 26px; flex: none; }
  .photo {
    position: absolute; border-radius: 50%;
    border: 6px solid var(--card);
    box-shadow: 0 2px 6px rgba(0,0,0,.15);
  }
  .photo--projector {
    left: 735px; top: 11px; width: 172px; height: 172px;
    background: radial-gradient(circle at 45% 55%, var(--brand-pale) 0, var(--brand-mid) 25%, #1d3f58 70%);
  }
  .photo--ledwall {
    left: 744px; top: 196px; width: 180px; height: 180px;
    background: linear-gradient(180deg, #f4f4f4, #d9dcdf);
  }
  .photo--board {
    left: 695px; top: 378px; width: 174px; height: 174px;
    background: radial-gradient(circle at 55% 40%, var(--brand-soft) 0, var(--brand-mid) 40%, #0b2d5a 90%);
  }
</style>
</head>
<body>
  <main class="card">
    <svg class="card__panel" width="1000" height="568" viewBox="0 0 1000 568" aria-hidden="true">
      <path d="M800 0 C835 70 840 170 846 250 C850 360 770 480 718 568 L1000 568 L1000 0 Z" fill="var(--brand-deep)"/>
    </svg>

    <div class="brand">
      <span class="brand__dot"></span>
      <span class="brand__name">CORVY</span>
      <span class="brand__line">ELECTRONIC REPAIRS</span>
    </div>

    <p class="intro">Electronic Repairs for<br>OEM's Industrial electronic repairs,<br>consumer audio visual, Projectors</p>

    <ul class="services">
      <li><svg viewBox="0 0 26 26"><circle cx="13" cy="13" r="13" fill="var(--brand-mid)"/><path d="M7 13.5l4 4 8-8.5" fill="none" stroke="#fff" stroke-width="3" stroke-linecap="round" stroke-linejoin="round"/></svg>Projector</li>
      <li><svg viewBox="0 0 26 26"><circle cx="13" cy="13" r="13" fill="var(--brand-mid)"/><path d="M7 13.5l4 4 8-8.5" fill="none" stroke="#fff" stroke-width="3" stroke-linecap="round" stroke-linejoin="round"/></svg>Led wall image</li>
      <li><svg viewBox="0 0 26 26"><circle cx="13" cy="13" r="13" fill="var(--brand-mid)"/><path d="M7 13.5l4 4 8-8.5" fill="none" stroke="#fff" stroke-width="3" stroke-linecap="round" stroke-linejoin="round"/></svg>Board Repair</li>
    </ul>

    <div class="photo photo--projector" role="img" aria-label="Photo of a ceiling-mounted projector being serviced"></div>
    <div class="photo photo--ledwall" role="img" aria-label="Image of an LED video wall on a stand"></div>
    <div class="photo photo--board" role="img" aria-label="Close-up photo of an electronic circuit board under repair"></div>
  </main>
</body>
</html>
```